VelkaVision.com

Complete Website Design (Godaddy) and company Branding / Logo Design. The products will sell are only done in-person and are installed. So this site does not need to be an e-commerce site. We will only be giving out information and collecting customer inquires. Website will only need to be about 3 to 5 pages.

```html
<!DOCTYPE html>
<html lang="en">
<head>
<meta charset="utf-8">
<title>VelkaVision</title>
<link href="https://fonts.googleapis.com/css2?family=Barlow:wght@400;500;600;700&family=Inter:wght@400;500;600&display=swap" rel="stylesheet">
<style>
:root{
  --brand:#0452a4;
  --ink:#1c1c1c;
  --muted:#555a60;
  --white:#ffffff;
  --soft:#ececec;
  --field-line:#d2d4d8;
  --req:#e03030;
}
*{box-sizing:border-box;margin:0;padding:0}
html,body{width:680px;height:1200px;overflow:hidden;background:var(--white)}
body{position:relative;font-family:"Barlow",Arial,sans-serif;color:var(--ink)}
.abs{position:absolute}

/* header */
.site-header{left:0;top:0;width:680px;height:42px;background:var(--brand)}
.brand-name{left:81px;top:11px;font-weight:700;font-size:11px;color:var(--white);letter-spacing:.1px}
.main-nav a{position:absolute;top:15px;font-size:7.6px;color:var(--white);text-decoration:none}
.nav-active{left:323px;top:0;width:22px;height:2px;background:var(--white)}
.header-cta{left:538px;top:11px;width:60px;height:18px;background:var(--white);color:var(--brand);font-weight:600;font-size:7.6px;display:flex;align-items:center;justify-content:center}

/* hero */
.hero-band{left:0;top:42px;width:81px;height:317px;background:var(--brand)}
.hero-photo{left:81px;top:42px;width:599px;height:317px;
  background:linear-gradient(90deg,#fbfbfb 0%,#f4f3f2 38%,#d9cfc6 55%,#8f7a68 70%,#c9b8a6 85%,#e6dfd8 100%)}
.side-line{left:41px;width:1.4px;height:53px;background:rgba(255,255,255,.75)}
.side-dot{left:32px;width:19px;height:19px;border:1px solid var(--white);border-radius:50%}
.hero-title{left:122px;top:125px;font-weight:700;font-size:23px;letter-spacing:.2px;color:var(--ink)}
.hero-text{left:122px;top:157px;width:175px;font-size:7.2px;line-height:11.3px;color:var(--muted)}
.btn{background:var(--brand);color:var(--white);font-weight:600;display:flex;align-items:center;justify-content:center}
.hero-btn{left:122px;top:200px;width:59px;height:18px;font-size:7.6px}
.slide-arrow{top:310px;width:20px;height:20px;border-radius:50%;background:#6b6b6b;display:flex;align-items:center;justify-content:center}

/* about */
.about-frame{left:82px;top:419px;width:241px;height:204px;background:var(--brand)}
.about-photo{left:82px;top:418px;width:223px;height:187px;
  background:linear-gradient(135deg,#cfd8da 0%,#b9c3c6 35%,#a68d7f 65%,#c9b7a8 100%)}
.about-title{left:348px;top:415px;font-weight:700;font-size:21px;color:var(--ink)}
.about-text{left:348px;top:447px;width:250px;font-size:7.1px;line-height:11.3px;color:var(--muted);text-align:justify}
.about-btn{left:348px;top:582px;width:59px;height:17px;font-size:7.6px}

/* contact form */
.contact{left:0;top:683px;width:680px;height:306px;
  background:linear-gradient(120deg,#efefef 0%,#e4e4e6 40%,#f0f0f0 70%,#e6e6e7 100%)}
.contact-title{left:0;top:727px;width:680px;text-align:center;font-weight:700;font-size:21px;color:var(--ink)}
.field-label{font-family:"Inter",Arial,sans-serif;font-size:7.4px;color:#6a6a6a}
.field-label span{color:var(--req)}
.field{background:var(--white);border:1px solid var(--field-line);border-radius:2px}
.submit-btn{left:302px;top:910px;width:76px;height:23px;font-family:"Inter",Arial,sans-serif;font-size:7.6px}

/* footer */
.site-footer{left:0;top:989px;width:680px;height:211px;background:var(--brand);color:var(--white)}
.footer-brand{left:105px;top:1041px;font-weight:700;font-size:15.5px;color:var(--white)}
.foot-dot{top:1079px;width:18px;height:18px;border:1px solid var(--white);border-radius:50%}
.footer-heading{top:1043px;font-weight:500;font-size:10px;color:var(--white);letter-spacing:.2px}
.contact-icon{left:276px;width:19px;height:19px;border-radius:50%;background:var(--white);display:flex;align-items:center;justify-content:center}
.contact-line{left:299px;font-family:"Inter",Arial,sans-serif;font-size:7.4px;line-height:11.3px;color:var(--white)}
.news-input{left:439px;top:1067px;width:136px;height:22px;border:1px solid var(--white);border-radius:2px;font-family:"Inter",Arial,sans-serif;font-size:6.6px;padding-left:8px;display:flex;align-items:center;color:var(--white)}
.news-btn{left:440px;top:1096px;width:57px;height:20px;background:var(--white);color:var(--ink);border-radius:1px;font-family:"Inter",Arial,sans-serif;font-weight:600;font-size:6.4px;display:flex;align-items:center;justify-content:center}
.copyright{left:0;top:1169px;width:680px;text-align:center;font-family:"Inter",Arial,sans-serif;font-size:7.4px;color:var(--white)}
</style>
</head>
<body>

<header class="abs site-header"></header>
<div class="abs brand-name">VELKA VISION</div>
<div class="abs nav-active"></div>
<nav class="main-nav">
  <a style="left:324px">Home</a>
  <a style="left:359px">About</a>
  <a style="left:395px">Services</a>
  <a style="left:439px">Blog</a>
  <a style="left:469px">Contact</a>
</nav>
<div class="abs header-cta">Get In Touch</div>

<section>
  <div class="abs hero-band"></div>
  <div class="abs hero-photo" role="img" aria-label="Two installers in overalls mounting a large flat-screen TV above a wooden media console"></div>
  <div class="abs side-line" style="top:102px"></div>
  <div class="abs side-dot" style="top:164px"></div>
  <div class="abs side-dot" style="top:192px"></div>
  <div class="abs side-dot" style="top:219px"></div>
  <div class="abs side-line" style="top:247px"></div>
  <h1 class="abs hero-title">VELKA VISION</h1>
  <p class="abs hero-text">Lorem ipsum dolor sit amet, consectetur adipiscing elit, sed do eiusmod tempor incididunt ut labore et dolore magna aliqua.</p>
  <div class="abs btn hero-btn">Get Started</div>
  <div class="abs slide-arrow" style="left:121px">
    <svg width="6" height="6" viewBox="0 0 6 6"><path d="M4 1 L2 3 L4 5" stroke="#fff" stroke-width="0.9" fill="none"/></svg>
  </div>
  <div class="abs slide-arrow" style="left:143px">
    <svg width="6" height="6" viewBox="0 0 6 6"><path d="M2 1 L4 3 L2 5" stroke="#fff" stroke-width="0.9" fill="none"/></svg>
  </div>
</section>

<section>
  <div class="abs about-frame"></div>
  <div class="abs about-photo" role="img" aria-label="Technician repairing a television while a customer waits on a sofa"></div>
  <h2 class="abs about-title">ABOUT US</h2>
  <p class="abs about-text">Lorem ipsum dolor sit amet, consectetur adipiscing elit, sed do eiusmod tempor incididunt ut labore et dolore magna aliqua. Ut enim ad minim veniam, quis nostrud exercitation ullamco laboris nisi ut aliquip ex ea commodo consequat. Duis aute irure dolor in reprehenderit in voluptate velit esse cillum dolore eu fugiat nulla pariatur. Excepteur sint occaecat cupidatat non proident, sunt in culpa qui officia deserunt mollit anim id est laborum. Lorem ipsum dolor sit amet, consectetur adipiscing elit, sed do eiusmod tempor incididunt ut labore et dolore magna aliqua. Ut enim ad minim veniam, quis nostrud exercitation ullamco laboris nisi ut aliquip ex ea commodo consequat. Duis aute irure dolor in reprehenderit in voluptate velit esse cillum dolore eu fugiat nulla pariatur.</p>
  <div class="abs btn about-btn">Read More</div>
</section>

<section>
  <div class="abs contact"></div>
  <h2 class="abs contact-title">GET IN TOUCH</h2>
  <div class="abs field-label" style="left:136px;top:767px">First name <span>*</span></div>
  <div class="abs field-label" style="left:277px;top:767px">Last name <span>*</span></div>
  <div class="abs field-label" style="left:417px;top:767px">Email <span>*</span></div>
  <div class="abs field" style="left:134px;top:781px;width:132px;height:29px"></div>
  <div class="abs field" style="left:274px;top:781px;width:132px;height:29px"></div>
  <div class="abs field" style="left:415px;top:781px;width:132px;height:29px"></div>
  <div class="abs field-label" style="left:136px;top:822px">Message <span>*</span></div>
  <div class="abs field" style="left:134px;top:835px;width:413px;height:66px"></div>
  <div class="abs btn submit-btn">Submit Now</div>
</section>

<footer>
  <div class="abs site-footer"></div>
  <div class="abs footer-brand">VELKA VISION</div>
  <div class="abs foot-dot" style="left:108px"></div>
  <div class="abs foot-dot" style="left:130px"></div>
  <div class="abs foot-dot" style="left:153px"></div>

  <div class="abs footer-heading" style="left:276px">CONTACT US</div>
  <div class="abs contact-icon" style="top:1067px">
    <svg width="8" height="8" viewBox="0 0 8 8"><path d="M4 0.6 C2.5 0.6 1.6 1.7 1.6 2.9 C1.6 4.6 4 7.4 4 7.4 C4 7.4 6.4 4.6 6.4 2.9 C6.4 1.7 5.5 0.6 4 0.6 Z" fill="var(--brand)"/><circle cx="4" cy="2.9" r="0.9" fill="#fff"/></svg>
  </div>
  <div class="abs contact-line" style="top:1066px">123, Lorem ipsum dolor sit<br>amet, consectetur</div>
  <div class="abs contact-icon" style="top:1098px">
    <svg width="8" height="8" viewBox="0 0 8 8"><path d="M1.6 1 L2.9 1 L3.4 2.6 L2.6 3.2 C3 4.1 3.9 5 4.8 5.4 L5.4 4.6 L7 5.1 L7 6.4 C7 6.8 6.6 7.1 6.2 7 C3.6 6.6 1.4 4.4 1 1.8 C0.9 1.4 1.2 1 1.6 1 Z" fill="var(--brand)"/></svg>
  </div>
  <div class="abs contact-line" style="top:1102px">+1 888 888 8888</div>
  <div class="abs contact-icon" style="top:1122px">
    <svg width="8" height="8" viewBox="0 0 8 8"><rect x="0.8" y="1.8" width="6.4" height="4.6" rx="0.5" fill="var(--brand)"/><path d="M1 2.1 L4 4.3 L7 2.1" stroke="#fff" stroke-width="0.6" fill="none"/></svg>
  </div>
  <div class="abs contact-line" style="top:1125px">info@velkavision.com</div>

  <div class="abs footer-heading" style="left:439px">NEWSLETTER</div>
  <div class="abs news-input">Email address</div>
  <div class="abs news-btn">SUBSCRIBE</div>

  <div class="abs copyright">© Copyrights 2024 | all Rights Reserved</div>
</footer>

</body>
</html>
```